Classy, Elegant, Simple Business Card Design

Looking to have a classy, simple, and elegant design. Want a top notch designed business card. I really like the look of the new torvane credit card. I also like the design I attached. I am trying to reach 21-29 year old females for booking us for there wedding or event. We offer Disc Jockey Service, Photo Booth Rentals, and Uplighting .

Target Market(s)

21-28 year old females

Contact Information for Business Card

Has to have logo, website, email, and phone number

Font styles to use
Other font styles liked:
• open to font choice, modern, clean
Designer to choose
33a6d7
0791cd
0555a3
ffffff

Requirements
Must have
• Has to have logo, website, email, and phone number
Nice to have
• I really like the design of the new torvane credit card. I also included my logo and some designs I like
Should not have
• clutter or too much info

```html
<!DOCTYPE html>
<html lang="en">
<head>
<meta charset="utf-8">
<title>Brightnote Event Group – Business Card</title>
<link rel="stylesheet" href="https://fonts.googleapis.com/css2?family=Josefin+Sans:wght@400&family=Roboto:wght@400;700&display=swap">
<style>
  :root {
    --backdrop: #b3b3b3;
    --card: #f1f1f1;
    --card-edge: #e4e4e4;
    --navy: #0e3a70;
    --royal: #0555a3;
    --azure: #0791cd;
    --sky: #33a6d7;
    --ink: #1d2a3a;
    --white: #ffffff;
  }
  * { margin: 0; padding: 0; box-sizing: border-box; }
  html, body { width: 1200px; height: 576px; overflow: hidden; }
  body {
    background: var(--backdrop);
    position: relative;
    font-family: "Roboto", Arial, sans-serif;
  }
  .card {
    position: absolute;
    width: 482px;
    height: 294px;
    background: linear-gradient(180deg, var(--white) 0%, var(--card) 60%, var(--card-edge) 100%);
    border-radius: 10px;
    overflow: hidden;
    box-shadow: 0 3px 8px rgba(0,0,0,0.25);
  }
  .card--front { left: 82px; top: 139px; }
  .card--back { left: 602px; top: 138px; }

  .brand {
    position: absolute;
    display: flex;
    flex-direction: column;
    align-items: center;
    font-family: "Josefin Sans", "Century Gothic", sans-serif;
    font-weight: 400;
    color: var(--royal);
    text-align: center;
  }
  .brand__mark {
    width: 58px; height: 58px;
    border-radius: 50%;
    background: var(--azure);
    margin-bottom: 14px;
  }
  .brand__name { font-size: 30px; letter-spacing: 0.5px; line-height: 1; }
  .brand__tagline { font-size: 12px; letter-spacing: 6px; margin-top: 6px; line-height: 1; }

  .card--front .brand { left: 0; right: 0; top: 66px; }
  .card--back .brand { left: 14px; width: 226px; top: 58px; }

  .equalizer-strip {
    position: absolute;
    left: 0; right: 0; bottom: 0;
    height: 44px;
    background: linear-gradient(180deg, rgba(51,166,215,0) 0%, rgba(7,145,205,0.55) 45%, var(--navy) 100%);
  }

  .wave { position: absolute; inset: 0; width: 100%; height: 100%; }

  .holder {
    position: absolute;
    right: 25px; top: 48px;
    text-align: right;
  }
  .holder__name { font-size: 19px; font-weight: 700; color: var(--royal); line-height: 1.1; }
  .holder__title { font-size: 11.5px; color: var(--ink); margin-top: 4px; }

  .contact {
    position: absolute;
    right: 22px; top: 209px;
    list-style: none;
    color: var(--white);
    font-size: 11.5px;
  }
  .contact__item {
    display: flex;
    justify-content: flex-end;
    align-items: center;
    gap: 7px;
    height: 18.5px;
  }
  .contact__icon { width: 11px; height: 11px; fill: none; stroke: var(--sky); stroke-width: 1.4; }
  .contact__icon--solid { fill: var(--sky); stroke: none; }
</style>
</head>
<body>

<section class="card card--front" aria-label="Card front">
  <div class="brand">
    <span class="brand__mark"></span>
    <span class="brand__name">BRIGHTNOTE</span>
    <span class="brand__tagline">EVENT GROUP</span>
  </div>
  <div class="equalizer-strip" role="img" aria-label="Row of blue sound equalizer bars along the bottom edge"></div>
</section>

<section class="card card--back" aria-label="Card back">
  <div class="brand">
    <span class="brand__mark"></span>
    <span class="brand__name">BRIGHTNOTE</span>
    <span class="brand__tagline">EVENT GROUP</span>
  </div>

  <div class="holder">
    <p class="holder__name">Daniel Reyes</p>
    <p class="holder__title">Founder &amp; CEO</p>
  </div>

  <svg class="wave" viewBox="0 0 482 294" preserveAspectRatio="none" aria-hidden="true">
    <defs>
      <linearGradient id="bar-fade" x1="0" y1="0" x2="0" y2="1">
        <stop offset="0" stop-color="#33a6d7" stop-opacity="0"/>
        <stop offset="1" stop-color="#0555a3" stop-opacity="0.7"/>
      </linearGradient>
    </defs>
    <g role="img" aria-label="Sound equalizer bars rising along the wave edge">
      <path d="M0 250 C150 250 220 236 300 188 S420 146 482 144 L482 176 C420 178 380 186 300 220 S150 282 0 282 Z" fill="url(#bar-fade)"/>
    </g>
    <path d="M0 282 C150 282 220 268 300 220 S420 178 482 176" fill="none" stroke="#ffffff" stroke-width="5"/>
    <path d="M0 286 C150 286 220 272 300 224 S420 182 482 180 L482 294 L0 294 Z" fill="#0e3a70"/>
  </svg>

  <ul class="contact">
    <li class="contact__item">555 0142 0187
      <svg class="contact__icon contact__icon--solid" viewBox="0 0 12 12" aria-hidden="true"><path d="M1 3.5 Q6 0 11 3.5 L9.5 5 L8 4 L8 3 Q6 2.2 4 3 L4 4 L2.5 5 Z M3 6 H9 L10 10 H2 Z"/></svg>
    </li>
    <li class="contact__item">daniel@brightnote.com
      <svg class="contact__icon contact__icon--solid" viewBox="0 0 12 12" aria-hidden="true"><path d="M1 2.5 H11 L6 6.5 Z M1 3.8 L6 7.8 L11 3.8 V9.5 H1 Z"/></svg>
    </li>
    <li class="contact__item">www.brightnote.com
      <svg class="contact__icon" viewBox="0 0 12 12" aria-hidden="true"><circle cx="6" cy="6" r="4.6"/><ellipse cx="6" cy="6" rx="2" ry="4.6"/><path d="M1.4 6 H10.6"/></svg>
    </li>
  </ul>
</section>

</body>
</html>
```